Verodex business card

Business card for sustainable investment company called "Verodex". Verodex is an exchange platform selling carbon credits between buyers and sellers. Carbon Credits are an environmental commodity for reducing global carbon emissions.

the card should obviously have our logo and the theme should be sustainability/environment mixed with a trading platform.

Contact Information for Business Card

Logo, Name, Title, Phone, Email

Colors
0054AA
0677BA
7BADD7
CADEEF
E8F1F8
0094D4
00A9DD
6FCCEA
C7EBF8
E9F6FB
00AB8E
00BBA5
67D7C9
C6EFE9
E9F9F6
59FF00
82FF00
B8FF75
E3FFCB
F4FFEA

```html
<!DOCTYPE html>
<html lang="en">
<head>
<meta charset="utf-8">
<title>Verodex business card</title>
<link href="https://fonts.googleapis.com/css2?family=Montserrat:wght@500;600;700&family=Raleway:wght@400;500&display=swap" rel="stylesheet">
<style>
  :root {
    --backdrop: #8e8e8e;
    --card-dark: #0b0b0b;
    --card-dark-mid: #262626;
    --accent-blue: #1e90e6;
    --accent-cyan: #35e8ee;
    --accent-deep: #1f6cec;
    --text-light: #ffffff;
  }
  html, body {
    margin: 0;
    width: 1200px;
    height: 1200px;
    overflow: hidden;
    background: var(--backdrop);
  }
  .canvas {
    position: relative;
    width: 1200px;
    height: 1200px;
  }
  .card {
    position: absolute;
    left: 281px;
    width: 641px;
    height: 366px;
    border-radius: 20px;
    overflow: hidden;
  }
  .card-front { top: 195px; }
  .card-back { top: 639px; }
  .card-surface {
    position: absolute;
    inset: 0;
  }
  .card-front .card-surface {
    background: radial-gradient(ellipse at 50% 45%, var(--card-dark-mid) 0%, #151515 55%, var(--card-dark) 100%);
  }
  .card-back .card-surface {
    background: linear-gradient(135deg, var(--accent-cyan) 0%, #30c4ec 40%, #2a8ff0 75%, var(--accent-deep) 100%);
  }
  .brand {
    position: absolute;
    display: flex;
    align-items: center;
    gap: 34px;
    height: 88px;
  }
  .card-front .brand { left: 84px; top: 79px; }
  .card-back .brand { left: 83px; top: 141px; }
  .brand-dot {
    width: 88px;
    height: 88px;
    border-radius: 50%;
    flex: none;
  }
  .card-front .brand-dot { background: var(--accent-blue); }
  .card-back .brand-dot { background: var(--text-light); }
  .brand-name {
    font-family: "Montserrat", sans-serif;
    font-weight: 600;
    font-size: 64px;
    letter-spacing: 0.5px;
    color: var(--text-light);
    line-height: 1;
  }
  .person {
    position: absolute;
    right: 330px;
    top: 234px;
    text-align right;
    text-align: right;
  }
  .person-name {
    font-family: "Montserrat", sans-serif;
    font-weight: 600;
    font-size: 32px;
    color: var(--accent-blue);
    line-height: 1.1;
    margin: 0;
    white-space: nowrap;
  }
  .person-title {
    font-family: "Raleway", sans-serif;
    font-weight: 500;
    font-size: 17px;
    color: var(--text-light);
    margin: 2px 0 0;
    white-space: nowrap;
  }
  .contacts {
    position: absolute;
    left: 345px;
    top: 227px;
    list-style: none;
    margin: 0;
    padding: 0;
  }
  .contact-item {
    display: flex;
    align-items: center;
    gap: 8px;
    height: 22.5px;
    font-family: "Raleway", sans-serif;
    font-weight: 400;
    font-size: 17px;
    color: var(--text-light);
    white-space: nowrap;
  }
  .contact-icon {
    width: 14px;
    height: 14px;
    flex: none;
  }
</style>
</head>
<body>
<main class="canvas">
  <section class="card card-front">
    <div class="card-surface" role="img" aria-label="Dark carbon-fibre texture background"></div>
    <div class="brand">
      <span class="brand-dot"></span>
      <span class="brand-name">VERODEX</span>
    </div>
    <div class="person">
      <p class="person-name">MARCUS HALE</p>
      <p class="person-title">Founder &amp; CEO</p>
    </div>
    <ul class="contacts">
      <li class="contact-item">
        <svg class="contact-icon" viewBox="0 0 16 16"><path d="M3 1.5l3 .5 1 3.5-2 1.5c1 2 2.5 3.5 4.5 4.5l1.5-2 3.5 1 .5 3-2 1.5C7 14.5 1.5 9 1.5 3.5z" fill="var(--accent-blue)"/></svg>
        <span>(555) 014-2387</span>
      </li>
      <li class="contact-item">
        <svg class="contact-icon" viewBox="0 0 16 16"><rect x="1" y="3" width="14" height="10" fill="var(--accent-blue)"/><path d="M1 3l7 6 7-6" fill="none" stroke="#0b0b0b" stroke-width="1.3"/></svg>
        <span>office@verodex.com</span>
      </li>
      <li class="contact-item">
        <svg class="contact-icon" viewBox="0 0 16 16"><circle cx="8" cy="8" r="7" fill="var(--accent-blue)"/><path d="M4 4.5c2 0 2 2 3.5 2.5s0 3 1.5 4M11 3.5c-1 1.5 0 3 1.5 3.5" fill="none" stroke="#0b0b0b" stroke-width="1.2"/></svg>
        <span>verodex.com</span>
      </li>
    </ul>
  </section>

  <section class="card card-back">
    <div class="card-surface" role="img" aria-label="Cyan to blue gradient with fine diagonal texture"></div>
    <div class="brand">
      <span class="brand-dot"></span>
      <span class="brand-name">VERODEX</span>
    </div>
  </section>
</main>
</body>
</html>
```